We are a recruitment company based in Norwich/Cambridge England.
I have included our company logo which we want to remain the same.

What we are looking for is a new creative Business card which will really stand out!!

Contact Information for Business Card

Harriet Dunmore
email: Harriet@plavex.co.uk
Address: Brackwell House
Fenmoor Enterprise Park
Partridge Way
Norwich
QB9 3KX
Tel:01632 960418

```html
<!DOCTYPE html>
<html lang="en">
<head>
<meta charset="utf-8">
<title>Plavex business card</title>
<link href="https://fonts.googleapis.com/css2?family=Montserrat:wght@500;700&family=Arimo:wght@400;700&display=swap" rel="stylesheet">
<style>
  :root {
    --stage: #2b2b2d;
    --card-grey: #8c878b;
    --band-grey: #8e898d;
    --pattern-grey: #989397;
    --brand-green: #8cc63f;
    --text-grey: #7d787c;
    --soft-green: #eef4e3;
    --soft-grey: #f0eff0;
    --white: #ffffff;
  }
  * { margin: 0; padding: 0; box-sizing: border-box; }
  html, body { width: 1200px; height: 880px; overflow: hidden; }
  body { background: var(--stage); position: relative; font-family: "Arimo", Arial, sans-serif; }

  .card {
    position: absolute;
    width: 600px;
    height: 343px;
    border-radius: 22px;
    overflow: hidden;
    box-shadow: 0 12px 30px rgba(0,0,0,0.45);
  }

  /* Back card */
  .card-back { left: 80px; top: 70px; background: var(--card-grey); }
  .card-back .pattern-area {
    position: absolute; inset: 0;
    background: radial-gradient(circle at 50% 50%, var(--pattern-grey), var(--card-grey) 75%);
  }
  .card-back .brand {
    position: absolute; left: 0; right: 0; top: 120px;
    display: flex; justify-content: center; align-items: center; gap: 16px;
  }
  .brand-dot { width: 58px; height: 58px; border-radius: 50%; background: var(--white); }
  .brand-name {
    font-family: "Montserrat", sans-serif; font-weight: 700; font-size: 56px;
    color: var(--white); letter-spacing: -1px; line-height: 1;
  }
  .card-back .website {
    position: absolute; left: 0; right: 0; top: 232px; text-align: center;
    color: var(--white); font-size: 15px; letter-spacing: 4px;
  }

  /* Front card */
  .card-front { left: 520px; top: 460px; background: var(--white); }
  .card-front .decor-area {
    position: absolute; left: 40px; top: 80px; width: 300px; height: 200px;
    border-radius: 50%;
    background: radial-gradient(ellipse at 40% 45%, var(--soft-grey) 0%, var(--soft-green) 55%, rgba(255,255,255,0) 72%);
  }
  .card-front .brand {
    position: absolute; right: 50px; top: 42px;
    display: flex; align-items: center; gap: 12px;
  }
  .card-front .brand-dot { width: 48px; height: 48px; background: var(--brand-green); }
  .card-front .brand-name { font-size: 44px; color: var(--text-grey); }

  .person { position: absolute; left: 40px; top: 205px; }
  .person-name { font-weight: 700; font-size: 26px; color: var(--brand-green); line-height: 1.05; }
  .person-role { font-size: 17px; color: var(--text-grey); line-height: 1.1; }
  .name-rule { position: absolute; left: 40px; right: 40px; top: 258px; height: 2px; background: var(--brand-green); }

  .contact-band {
    position: absolute; left: 0; right: 0; top: 272px; height: 50px;
    background: var(--band-grey);
    display: flex; align-items: center; padding: 0 22px; gap: 14px;
    color: var(--white); font-size: 11.5px;
  }
  .contact-group { display: flex; flex-direction: column; gap: 3px; }
  .contact-line { display: flex; align-items: center; gap: 6px; white-space: nowrap; }
  .contact-line svg { width: 13px; height: 13px; flex: none; }
  .divider { width: 1px; height: 30px; background: var(--white); opacity: 0.8; }
  .address { line-height: 1.3; }
  .green-strip { position: absolute; left: 0; right: 0; top: 325px; height: 18px; background: var(--brand-green); }
</style>
</head>
<body>

<section class="card card-back">
  <div class="pattern-area" role="img" aria-label="Repeating brand pattern background"></div>
  <div class="brand">
    <span class="brand-dot"></span>
    <span class="brand-name">Plavex</span>
  </div>
  <p class="website">www.plavex.co.uk</p>
</section>

<section class="card card-front">
  <div class="decor-area" role="img" aria-label="Large faint brand decoration"></div>
  <div class="brand">
    <span class="brand-dot"></span>
    <span class="brand-name">Plavex</span>
  </div>

  <div class="person">
    <p class="person-name">Harriet Dunmore</p>
    <p class="person-role">CEO</p>
  </div>
  <div class="name-rule"></div>

  <div class="contact-band">
    <div class="contact-group">
      <div class="contact-line">
        <svg viewBox="0 0 16 16"><circle cx="8" cy="8" r="7.5" fill="none" stroke="#fff"/><path d="M5 4.5l1.5-.5 1 2-1 .8a5 5 0 0 0 2.7 2.7l.8-1 2 1-.5 1.5c-3.5 0-6.5-3-6.5-6.5z" fill="#fff"/></svg>
        <span>01632 960418</span>
      </div>
      <div class="contact-line">
        <svg viewBox="0 0 16 16"><circle cx="8" cy="8" r="7.5" fill="none" stroke="#fff"/><rect x="4.5" y="4" width="7" height="8" rx="1" fill="#fff"/></svg>
        <span>01632 960771</span>
      </div>
    </div>
    <span class="divider"></span>
    <div class="contact-group">
      <div class="contact-line">
        <svg viewBox="0 0 16 16"><circle cx="8" cy="8" r="7.5" fill="none" stroke="#fff"/><rect x="4" y="5" width="8" height="6" fill="#fff"/><path d="M4 5l4 3.5L12 5" fill="none" stroke="#8e898d"/></svg>
        <span>Harriet@plavex.co.uk</span>
      </div>
      <div class="contact-line">
        <svg viewBox="0 0 16 16"><circle cx="8" cy="8" r="7.5" fill="none" stroke="#fff"/><circle cx="8" cy="8" r="4" fill="none" stroke="#fff"/><path d="M4 8h8M8 4v8" stroke="#fff"/></svg>
        <span>www.plavex.co.uk</span>
      </div>
    </div>
    <span class="divider"></span>
    <div class="contact-group address">
      <span>Brackwell House, Fenmoor Enterprise Park</span>
      <span>Partridge Way, Norwich QB9 3KX</span>
    </div>
  </div>
  <div class="green-strip"></div>
</section>

</body>
</html>
```